Heron Loan Partners Business Card

We need a business card design for our mortgage servicing company. In addition to servicing the loans of homeowners, we help homeowners with purchasing their homes and any mortgage refinancing. We would like to see designs that use the colors in the logo attached below (gold-ish yellow and navy blue), and any other design you deem fit! The design should communicate a simpler life with smart mortgages provided by Heron.

```html
<!DOCTYPE html>
<html lang="en">
<head>
<meta charset="utf-8">
<title>Heron Loan Partners Business Card</title>
<link rel="stylesheet" href="https://fonts.googleapis.com/css2?family=Montserrat:wght@400;500;700&display=swap">
<style>
  :root {
    --navy: #2b2763;
    --gold: #e0b23a;
    --ink: #1d1d22;
    --paper: #ffffff;
    --backdrop: #d9d9dc;
  }
  * { box-sizing: border-box; margin: 0; padding: 0; }
  html, body { width: 1200px; height: 900px; overflow: hidden; }
  body {
    background: var(--backdrop);
    font-family: "Montserrat", Arial, sans-serif;
    color: var(--ink);
    position: relative;
  }
  .card {
    position: absolute;
    left: 250px;
    width: 700px;
    height: 400px;
    background: var(--paper);
    box-shadow: 0 6px 18px rgba(0,0,0,0.25);
  }
  .card-front { top: 35px; }
  .card-back { top: 465px; }

  .brand {
    display: flex;
    align-items: center;
    gap: 14px;
    color: var(--navy);
    font-weight: 700;
    white-space: nowrap;
  }
  .brand-mark {
    background: var(--gold);
    border-radius: 50%;
    flex: none;
  }
  .card-front .brand {
    position: absolute;
    left: 0; right: 0; top: 0; bottom: 0;
    justify-content: center;
    font-size: 46px;
  }
  .card-front .brand-mark { width: 40px; height: 40px; }

  .card-back .brand {
    position: absolute;
    right: 48px;
    top: 62px;
    font-size: 24px;
    gap: 10px;
  }
  .card-back .brand-mark { width: 22px; height: 22px; }

  .holder {
    position: absolute;
    left: 0;
    top: 150px;
    padding-left: 46px;
  }
  .holder-bar {
    position: absolute;
    left: 0;
    top: 24px;
    width: 30px;
    height: 42px;
    background: var(--gold);
  }
  .holder-name {
    font-size: 22px;
    font-weight: 700;
    letter-spacing: 0.5px;
    color: var(--navy);
  }
  .holder-name .surname { color: var(--gold); }
  .holder-title {
    font-size: 19px;
    font-weight: 400;
    margin-top: 4px;
    color: var(--ink);
  }

  .address {
    position: absolute;
    right: 48px;
    top: 165px;
    text-align: right;
    font-size: 18px;
    line-height: 1.4;
  }

  .contacts {
    position: absolute;
    left: 250px;
    bottom: 40px;
    list-style: none;
    font-size: 19px;
    line-height: 1.6;
  }
  .contacts li { display: flex; align-items: center; gap: 14px; }
  .contacts svg { width: 20px; height: 20px; fill: var(--gold); flex: none; }
</style>
</head>
<body>
  <section class="card card-front" aria-label="Card front">
    <div class="brand">
      <span class="brand-mark"></span>
      <span class="brand-name">Heron Loan Partners</span>
    </div>
  </section>

  <section class="card card-back" aria-label="Card back">
    <div class="brand">
      <span class="brand-mark"></span>
      <span class="brand-name">Heron Loan Partners</span>
    </div>

    <div class="holder">
      <span class="holder-bar"></span>
      <p class="holder-name">DANE <span class="surname">WHITFIELD</span></p>
      <p class="holder-title">Owner</p>
    </div>

    <p class="address">4810 Linden Park Rd, Ste<br>210, Carver, TX 75390</p>

    <ul class="contacts">
      <li>
        <svg viewBox="0 0 24 24" aria-hidden="true"><path d="M6.6 10.8a15.1 15.1 0 0 0 6.6 6.6l2.2-2.2a1 1 0 0 1 1-.25 11.4 11.4 0 0 0 3.6.57 1 1 0 0 1 1 1V20a1 1 0 0 1-1 1A17 17 0 0 1 3 4a1 1 0 0 1 1-1h3.5a1 1 0 0 1 1 1c0 1.25.2 2.45.57 3.6a1 1 0 0 1-.25 1z"/></svg>
        555.014.2290
      </li>
      <li>
        <svg viewBox="0 0 24 24" aria-hidden="true"><path d="M2 5h20v14H2z M4 7v.4l8 5.2 8-5.2V7z" fill-rule="evenodd"/></svg>
        info@heronloanpartners.com
      </li>
      <li>
        <svg viewBox="0 0 24 24" aria-hidden="true"><path d="M12 2a10 10 0 1 0 0 20 10 10 0 0 0 0-20zm-1 17.9A8 8 0 0 1 4.1 11H8c.1 3 1 6 3 8.9zM8 9H4.1A8 8 0 0 1 11 4.1C9 7 8.1 8 8 9zm5 10.9c2-2.9 2.9-5.9 3-8.9h3.9a8 8 0 0 1-6.9 8.9zM16 9c-.1-1-1-2-3-4.9A8 8 0 0 1 19.9 9z"/></svg>
        www.heronloanpartners.com
      </li>
    </ul>
  </section>
</body>
</html>
```